Firm Stationery Design

I need a design for stationery, including: Stationery First Page, Stationery Second Sheet, Envelope, Mailing Label for Flat Envelopes, and Business Cards

```html
<!DOCTYPE html>
<html lang="en">
<head>
<meta charset="utf-8">
<title>Harlow Law LLC — Stationery</title>
<link rel="stylesheet" href="https://fonts.googleapis.com/css2?family=Montserrat:wght@400;500;700&family=Lato:wght@400&display=swap">
<style>
  :root{
    --ink:#1a1a1a;
    --orange:#f5a01e;
    --orange-deep:#e08a14;
    --paper:#ffffff;
    --ground:#ece6dc;
    --muted:#3b3b3b;
    --shadow:0 3px 6px rgba(60,40,20,.35);
  }
  *{box-sizing:border-box;margin:0;padding:0}
  html,body{width:1200px;height:884px;overflow:hidden}
  body{background:var(--ground);font-family:"Montserrat",sans-serif;color:var(--ink);position:relative}
  .sheet{position:absolute;background:var(--paper);box-shadow:var(--shadow)}
  .brand{display:flex;align-items:center;gap:5px;font-weight:700;color:var(--ink);white-space:nowrap;line-height:1}
  .brand-mark{background:var(--orange);flex:none}
  .brand.stacked{flex-direction:column;gap:10px;text-align:center}
  .rule-v{border-left:1px solid var(--orange)}
  .address{font-weight:400;color:var(--muted);line-height:1.35}
  .contact-list{list-style:none}
  .contact-list li{display:flex;align-items:center;gap:4px}
  .contact-list svg{flex:none}

  /* second sheet */
  .second-sheet{left:60px;top:109px;width:323px;height:242px}
  .second-sheet .head{position:absolute;left:22px;top:22px;display:flex;align-items:center;gap:8px}
  .second-sheet .brand{font-size:11px}
  .second-sheet .brand-mark{width:9px;height:9px}
  .second-sheet .address{font-size:8.2px;padding-left:7px;height:30px;display:flex;flex-direction:column;justify-content:center}

  /* note sheet */
  .note-sheet{left:425px;top:109px;width:179px;height:239px}
  .note-sheet .head{position:absolute;left:12px;top:15px;display:flex;align-items:center;gap:6px}
  .note-sheet .brand{font-size:7.5px;gap:3px}
  .note-sheet .brand-mark{width:6px;height:6px}
  .note-sheet .address{font-size:6px;padding-left:5px;height:22px;display:flex;flex-direction:column;justify-content:center}

  /* envelope back */
  .envelope{left:60px;top:422px;width:364px;height:160px;overflow:hidden}
  .envelope svg.flap{position:absolute;left:0;top:0}
  .envelope .brand{position:absolute;left:0;right:0;top:22px;justify-content:center;font-size:12px}
  .envelope .brand-mark{width:10px;height:10px}

  /* card front */
  .card-front{left:486px;top:413px;width:287px;height:163px;display:flex;align-items:center;justify-content:center}
  .card-front .brand{font-size:22px}
  .card-front .brand-mark{width:22px;height:22px}

  /* mailing label */
  .label{left:60px;top:618px;width:363px;height:157px}
  .label .head{position:absolute;left:15px;top:14px;display:flex;align-items:center;gap:7px}
  .label .brand{font-size:8.5px;gap:3px}
  .label .brand-mark{width:7px;height:7px}
  .label .address{font-size:6.2px;padding-left:7px;height:24px;display:flex;flex-direction:column;justify-content:center}

  /* business card back */
  .card-back{left:486px;top:612px;width:286px;height:163px;display:flex;align-items:center;padding-left:22px;gap:10px}
  .card-back .brand{font-size:11.5px;gap:4px}
  .card-back .brand-mark{width:9px;height:9px}
  .card-back .details{padding-left:11px;height:88px;display:flex;flex-direction:column;justify-content:center}
  .card-back .person{font-size:12.5px;font-weight:700;color:var(--orange);letter-spacing:.3px}
  .card-back .role{font-size:8.4px;color:var(--muted);margin:2px 0 8px}
  .card-back .address{font-size:8.4px;margin-bottom:6px}
  .card-back .contact-list{font-size:8.4px;color:var(--muted);line-height:1.4}

  /* letterhead */
  .letterhead{left:814px;top:193px;width:327px;height:463px;padding:0 31px}
  .letterhead .top{display:flex;justify-content:space-between;align-items:center;padding-top:18px;height:87px;border-bottom:1px solid var(--orange)}
  .letterhead .brand{font-size:10.5px;gap:4px}
  .letterhead .brand-mark{width:9px;height:9px}
  .letterhead .info{padding-left:8px;font-size:6.2px;color:var(--muted);line-height:1.35}
  .letterhead .info .address{margin-bottom:4px}
  .recipient{margin-top:36px;font-family:"Lato",sans-serif;color:var(--muted)}
  .recipient .name{font-size:6.2px;letter-spacing:.2px}
  .recipient .line{font-size:4.4px;margin-top:2px}
  .body-copy{margin-top:32px;font-family:"Lato",sans-serif;font-size:4.5px;line-height:1.78;color:var(--muted);text-align:justify}
  .body-copy p+p{margin-top:7px}
  .closing{margin-top:36px;font-family:"Lato",sans-serif;color:var(--muted)}
  .closing .sincerely{font-size:4.6px}
  .signature{display:block;width:40px;height:10px;margin:5px 0 2px;border-radius:5px;background:linear-gradient(90deg,#2a2a2a 0%,#5a5a5a 100%);opacity:.75}
  .closing .signer{font-size:6.2px}
</style>
</head>
<body>

<section class="sheet second-sheet" aria-label="Stationery second sheet">
  <div class="head">
    <div class="brand"><span class="brand-mark"></span>Harlow Law LLC</div>
    <div class="address rule-v"><span>Your address, City</span><span>State, Zip 1234</span></div>
  </div>
</section>

<section class="sheet note-sheet" aria-label="Note sheet">
  <div class="head">
    <div class="brand"><span class="brand-mark"></span>Harlow Law LLC</div>
    <div class="address rule-v"><span>Your address, City</span><span>State, Zip 1234</span></div>
  </div>
</section>

<section class="sheet envelope" aria-label="Envelope back">
  <svg class="flap" width="364" height="90" viewBox="0 0 364 90" aria-hidden="true">
    <defs>
      <linearGradient id="flapShade" x1="0" y1="0" x2="0" y2="1">
        <stop offset="0" stop-color="#000" stop-opacity=".12"/>
        <stop offset="1" stop-color="#000" stop-opacity="0"/>
      </linearGradient>
    </defs>
    <rect x="8" y="58" width="348" height="30" fill="url(#flapShade)"/>
    <path d="M2 0 L362 0 L350 42 Q344 57 324 57 L40 57 Q20 57 14 42 Z" fill="#fff" stroke="#e6e6e6" stroke-width=".8"/>
  </svg>
  <div class="brand"><span class="brand-mark"></span>Harlow Law LLC</div>
</section>

<section class="sheet card-front" aria-label="Business card front">
  <div class="brand stacked"><span class="brand-mark"></span>Harlow Law LLC</div>
</section>

<section class="sheet label" aria-label="Mailing label for flat envelopes">
  <div class="head">
    <div class="brand"><span class="brand-mark"></span>Harlow Law LLC</div>
    <div class="address rule-v"><span>Your address, City</span><span>State, Zip 1234</span></div>
  </div>
</section>

<section class="sheet card-back" aria-label="Business card back">
  <div class="brand"><span class="brand-mark"></span>Harlow Law LLC</div>
  <div class="details rule-v">
    <div class="person">DANIEL REYES</div>
    <div class="role">Managing Director</div>
    <div class="address">Your address, City<br>State, Zip 1234</div>
    <ul class="contact-list">
      <li><svg width="7" height="7" viewBox="0 0 10 10"><path d="M2 1h2l1 2.5-1.3 1a6 6 0 0 0 2.8 2.8l1-1.3L10 7v2a1 1 0 0 1-1 1A8 8 0 0 1 1 2a1 1 0 0 1 1-1z" fill="var(--orange)"/></svg>123 456 789</li>
      <li><svg width="7" height="7" viewBox="0 0 10 10"><rect x="0" y="2" width="10" height="7" fill="var(--orange)"/><path d="M0 2l5 4 5-4" stroke="#fff" fill="none"/></svg>info@harlowlawllc.com</li>
      <li><svg width="7" height="7" viewBox="0 0 10 10"><circle cx="5" cy="5" r="4.5" fill="var(--orange)"/><path d="M.5 5h9M5 .5c-2 2.5-2 6.5 0 9M5 .5c2 2.5 2 6.5 0 9" stroke="#fff" stroke-width=".7" fill="none"/></svg>www.harlowlawllc.com</li>
    </ul>
  </div>
</section>

<section class="sheet letterhead" aria-label="Stationery first page">
  <header class="top">
    <div class="brand"><span class="brand-mark"></span>Harlow Law LLC</div>
    <div class="info rule-v">
      <div class="address">Your address, City<br>State, Zip 1234</div>
      <ul class="contact-list">
        <li><svg width="5" height="5" viewBox="0 0 10 10"><path d="M2 1h2l1 2.5-1.3 1a6 6 0 0 0 2.8 2.8l1-1.3L10 7v2a1 1 0 0 1-1 1A8 8 0 0 1 1 2a1 1 0 0 1 1-1z" fill="var(--orange)"/></svg>123 456 789</li>
        <li><svg width="5" height="5" viewBox="0 0 10 10"><rect x="0" y="2" width="10" height="7" fill="var(--orange)"/><path d="M0 2l5 4 5-4" stroke="#fff" fill="none"/></svg>info@harlowlawllc.com</li>
        <li><svg width="5" height="5" viewBox="0 0 10 10"><circle cx="5" cy="5" r="4.5" fill="var(--orange)"/></svg>www.harlowlawllc.com</li>
      </ul>
    </div>
  </header>
  <div class="recipient">
    <div class="name">MARISSA COLE</div>
    <div class="line">Chief Exective Officer</div>
    <div class="line">City/State, Zip Code</div>
  </div>
  <div class="body-copy">
    <p>Thank you for meeting with our team last week to review the terms of your new agreement. We have prepared a summary of the key points we discussed, along with several notes on timing, filing steps and the documents we still need from your office before the next review.</p>
    <p>Our attorneys will contact you directly to arrange a short call this month. During that call we will walk through each open item, answer any questions you may have and confirm the schedule for signing once all parties have approved the final draft.</p>
    <p>Please keep this letter with your records. If anything in the summary does not match your understanding, let us know in writing and we will update the file promptly. We look forward to continuing our work together.</p>
  </div>
  <div class="closing">
    <div class="sincerely">Sincerely,</div>
    <span class="signature" role="img" aria-label="Handwritten signature"></span>
    <div class="signer">Owen Pratt</div>
  </div>
</section>

</body>
</html>
```